Corporate-Design für Steuerberatungsgesellschaft
Zielgruppe
Wir sind eine Steuerberatungsgesellschaft mit 10 Mitarbeitern im Norden von Deutschland, kurz vor der Ostseeküste. Unser Unternehmen besteht seit 30 Jahren. Wir betreuen vor allem Mandanten in kleinen und mittleren Unternehmen: von der Arztpraxis bis zum Bauunternehmen. Demnächst werden wir neue Räume beziehen. Diese sollen großzügiger und moderner werden, teilweise mit Glaswänden.
Aufgabenstellung
Unser bisheriges Farbkonzept war von bordeaux und creme geprägt (www.nordklar-steuer.de). Das muss aber nicht weiter bestehen. Das bisherige Logo finden wir inhaltlich recht treffend, aber es sollte moderner gestaltet werden. Der Schriftzug des Kanzleinamens soll an der Fassade in silbernen Buchstaben angebracht werden.

```html
<!DOCTYPE html>
<html lang="de">
<head>
<meta charset="utf-8">
<title>NORDA Velten – Briefumschlag</title>
<link rel="stylesheet" href="https://fonts.googleapis.com/css2?family=Cinzel:wght@500&family=Poppins:wght@400;500&display=swap">
<style>
  :root {
    --bordeaux: #931b29;
    --graphite: #3d4443;
    --paper: #f6f6f6;
    --ink: #333a39;
    --window: #bde0e4;
    --backdrop: #e4e7e4;
  }
  * { margin: 0; padding: 0; box-sizing: border-box; }
  html, body { width: 1200px; height: 1012px; overflow: hidden; }
  body { background: var(--backdrop); position: relative; font-family: "Poppins", sans-serif; color: var(--ink); }

  .envelope { position: absolute; left: 235px; width: 709px; height: 356px; background: var(--paper); overflow: hidden; }
  .envelope--front { top: 125px; }
  .envelope--back { top: 548px; }

  .side-band { position: absolute; left: 0; top: 0; width: 67px; height: 100%; background: var(--bordeaux); }

  .brand__mark { position: absolute; left: 87px; top: 123px; width: 22px; height: 22px; background: var(--bordeaux); }
  .brand__name { position: absolute; left: 126px; top: 117px; font-family: "Cinzel", serif; font-weight: 500; font-size: 23px; line-height: 28px; letter-spacing: 0.3px; color: var(--bordeaux); white-space: nowrap; }
  .brand__tagline { position: absolute; left: 127px; top: 151px; font-size: 7px; line-height: 8px; letter-spacing: 8.2px; color: var(--ink); white-space: nowrap; }

  .address-window { position: absolute; left: 33px; top: 180px; width: 293px; height: 130px; background: var(--window); border-radius: 6px; }

  .flap { position: absolute; left: 0; top: 0; width: 709px; height: 96px; }
  .flap-brand__name { position: absolute; top: 22px; left: 0; width: 709px; text-align: center; color: #fff; font-family: "Cinzel", serif; font-weight: 500; font-size: 31px; line-height: 36px; letter-spacing: 1px; white-space: nowrap; }
  .flap-brand__tagline { position: absolute; top: 57px; left: 0; width: 709px; text-align: center; color: #fff; font-size: 9px; line-height: 10px; letter-spacing: 14px; padding-left: 14px; white-space: nowrap; }

  .sender { position: absolute; left: 381px; top: 282px; font-size: 8.4px; line-height: 13.5px; font-style: normal; }
  .sender__name { color: var(--bordeaux); }
  .sender__firm { font-weight: 500; }

  .contact { position: absolute; left: 538px; top: 284px; list-style: none; font-size: 8.4px; line-height: 12.8px; }
  .contact li { display: flex; align-items: center; gap: 7px; }
  .contact svg { width: 9px; height: 9px; flex: none; }

  .bottom-band { position: absolute; left: 0; bottom: 0; width: 100%; height: 8px; background: var(--bordeaux); }
</style>
</head>
<body>
  <section class="envelope envelope--front">
    <div class="side-band"></div>
    <span class="brand__mark"></span>
    <div class="brand__name">NORDA VELTEN</div>
    <div class="brand__tagline">STEUERBERATUNG</div>
    <div class="address-window"></div>
  </section>

  <section class="envelope envelope--back">
    <svg class="flap" viewBox="0 0 709 96" aria-hidden="true">
      <path d="M0 0 H709 L676 88 Q673 96 664 96 H48 Q39 96 36 88 Z" fill="var(--graphite)"/>
    </svg>
    <div class="flap-brand__name">NORDA VELTEN</div>
    <div class="flap-brand__tagline">STEUERBERATUNG</div>

    <address class="sender">
      <div><span class="sender__name">NORDA</span> Velten</div>
      <div class="sender__firm">Steuerberatungsgesellschaft mbH</div>
      <div>Hafenweg 12</div>
      <div>D - 17390 Velten</div>
    </address>

    <ul class="contact">
      <li><svg viewBox="0 0 10 10"><circle cx="5" cy="5" r="5" fill="var(--bordeaux)"/><path d="M3.3 2.6 L4.4 3.8 L3.9 4.4 Q4.6 5.6 5.6 6.1 L6.2 5.6 L7.4 6.7 L6.8 7.4 Q4.8 7.3 3.2 5.2 Q2.6 4 2.7 3.2 Z" fill="#fff"/></svg>+49 (0) 3834 / 61 72 - 0</li>
      <li><svg viewBox="0 0 10 10"><circle cx="5" cy="5" r="5" fill="var(--bordeaux)"/><rect x="2.8" y="4" width="4.4" height="3" fill="#fff"/><rect x="3.6" y="2.6" width="2.8" height="1.6" fill="#fff"/></svg>+49 (0) 3834 / 61 72 - 49</li>
      <li><svg viewBox="0 0 10 10"><circle cx="5" cy="5" r="5" fill="var(--bordeaux)"/><rect x="2.6" y="3.3" width="4.8" height="3.4" fill="#fff"/><path d="M2.6 3.3 L5 5.2 L7.4 3.3" fill="none" stroke="var(--bordeaux)" stroke-width="0.6"/></svg>post@nordklar-steuer.de</li>
      <li><svg viewBox="0 0 10 10"><circle cx="5" cy="5" r="5" fill="var(--bordeaux)"/><circle cx="5" cy="5" r="2.4" fill="none" stroke="#fff" stroke-width="0.7"/><path d="M2.6 5 H7.4 M5 2.6 V7.4" stroke="#fff" stroke-width="0.5"/></svg>www.nordklar-steuer.de</li>
    </ul>

    <div class="bottom-band"></div>
  </section>
</body>
</html>
```